Business Card Design for Training Business

Clear Path Coaching is a new business that delivers training and other services with a focus on topics related to mental health and wellbeing, for example, Wellmind Response Course, Resilience etc. We have a strong focus on evidence-based psychology and neuroscience. I have a logo which I will upload with the brief, so please consider colours that work well with the logo.
Target Market(s)
Adults, workplaces (particularly government and not-for-profits)
Industry/Entity Type
Business
Contact Information for Business Card
Head Strong TrainingSamantha SellwoodDirector0438 770 850sam@headstrongtraining.com.auwww.headstrongtraining.com.au

```html
<!DOCTYPE html>
<html lang="en">
<head>
<meta charset="utf-8">
<title>Clear Path Coaching – Business Card</title>
<link rel="stylesheet" href="https://fonts.googleapis.com/css2?family=Open+Sans:wght@300;400;700&display=swap">
<style>
  :root {
    --backdrop: #ecebe8;
    --card: #ffffff;
    --card-shade: #f3f3f3;
    --ink: #222426;
    --ink-soft: #4a4d50;
    --brand-grey: #85888b;
    --teal: #2cc3c6;
    --rule: #cfcfcf;
  }
  * { box-sizing: border-box; margin: 0; padding: 0; }
  html, body {
    width: 1200px;
    height: 1022px;
    overflow: hidden;
    background: var(--backdrop);
    font-family: "Open Sans", Arial, sans-serif;
  }
  .stage {
    width: 1200px;
    height: 1022px;
    display: flex;
    align-items: center;
    justify-content: center;
  }
  .business-card {
    position: relative;
    width: 900px;
    height: 514px;
    background: linear-gradient(135deg, var(--card) 0%, var(--card-shade) 100%);
    border-radius: 16px;
    box-shadow: 0 14px 40px rgba(0,0,0,0.14);
    overflow: hidden;
  }
  .accent-edge {
    position: absolute;
    top: 0;
    right: 0;
    width: 60px;
    height: 514px;
  }
  .brand {
    position: absolute;
    left: 70px;
    top: 140px;
    width: 310px;
    display: flex;
    flex-direction: column;
    align-items: center;
  }
  .brand-mark {
    width: 110px;
    height: 110px;
    border-radius: 50%;
    border: 2px solid var(--teal);
    margin-bottom: 24px;
  }
  .brand-name {
    color: var(--brand-grey);
    font-size: 26px;
    font-weight: 400;
    letter-spacing: 0;
    text-align: center;
    line-height: 1.2;
    white-space: nowrap;
  }
  .divider {
    position: absolute;
    left: 418px;
    top: 130px;
    width: 2px;
    height: 250px;
    background: linear-gradient(to bottom, rgba(207,207,207,0), var(--rule) 30%, var(--rule) 70%, rgba(207,207,207,0));
  }
  .contact {
    position: absolute;
    left: 452px;
    top: 150px;
  }
  .person-name {
    font-size: 38px;
    font-weight: 700;
    color: var(--ink);
    letter-spacing: -0.3px;
    line-height: 1.15;
  }
  .person-role {
    font-size: 21px;
    font-weight: 400;
    color: var(--teal);
    margin-bottom: 22px;
  }
  .contact-list { list-style: none; }
  .contact-list li {
    display: flex;
    align-items: center;
    gap: 12px;
    font-size: 19px;
    font-weight: 300;
    color: var(--ink-soft);
    line-height: 1.55;
    white-space: nowrap;
  }
  .contact-icon {
    width: 16px;
    height: 16px;
    flex: none;
  }
</style>
</head>
<body>
<main class="stage">
  <section class="business-card">
    <svg class="accent-edge" viewBox="0 0 60 514" aria-hidden="true">
      <path d="M60 0 L44 0 Q18 257 44 514 L60 514 Z" fill="#f0f0f0"/>
      <path d="M44 0 Q18 257 44 514" fill="none" stroke="var(--teal)" stroke-width="6"/>
    </svg>

    <div class="brand">
      <div class="brand-mark"></div>
      <p class="brand-name">Clear Path Coaching</p>
    </div>

    <div class="divider"></div>

    <div class="contact">
      <h1 class="person-name">Rebecca Tanfield</h1>
      <p class="person-role">Director</p>
      <ul class="contact-list">
        <li>
          <svg class="contact-icon" viewBox="0 0 16 16" aria-hidden="true">
            <path d="M4 1.5 L6.2 4.8 L4.8 6.3 Q6.3 9.6 9.7 11.2 L11.2 9.8 L14.5 12 L13 14.5 Q6 14 1.5 3 Z" fill="var(--teal)"/>
          </svg>
          <span>0491 362 517</span>
        </li>
        <li>
          <svg class="contact-icon" viewBox="0 0 16 16" aria-hidden="true">
            <rect x="1.5" y="3.5" width="13" height="9" fill="none" stroke="var(--teal)" stroke-width="1.6"/>
            <path d="M1.5 3.5 L8 9 L14.5 3.5" fill="none" stroke="var(--teal)" stroke-width="1.6"/>
          </svg>
          <span>bec@clearpathcoaching.example.au</span>
        </li>
        <li>
          <svg class="contact-icon" viewBox="0 0 16 16" aria-hidden="true">
            <circle cx="8" cy="8" r="6.5" fill="none" stroke="var(--teal)" stroke-width="1.5"/>
            <ellipse cx="8" cy="8" rx="2.8" ry="6.5" fill="none" stroke="var(--teal)" stroke-width="1.2"/>
            <path d="M1.5 8 H14.5 M2.5 5 H13.5 M2.5 11 H13.5" stroke="var(--teal)" stroke-width="1.1"/>
          </svg>
          <span>www.clearpathcoaching.example.au</span>
        </li>
      </ul>
    </div>
  </section>
</main>
</body>
</html>
```